Low Ferry Guild - Wavering CD Cover

To prepare a CD Cover for the single "Wavering" by Low Ferry Guild.
You can hear the single here:
http://lowferryguild-band.example/listen/

The LFG logo and backdrop are also provided if you want to incorporate them into the CD cover design, though that isn't mandatory.

Song is about deciding on taking on a serious relationship, and leaving the single life behind.

Target Market(s)

Music listeners, 18-50 yrs old, into retro 80s, Marrowmen/Tide Rollers

Industry/Entity Type

Music Download

Requirements
Must have
• LFG logo
• Wavering title
Nice to have
• Use of backdrop, or facimile
Should not have
• Too obvious on the term Wavering

```html
<!DOCTYPE html>
<html lang="en">
<head>
<meta charset="utf-8">
<title>Low Ferry Guild – Wavering</title>
<link rel="stylesheet" href="https://fonts.googleapis.com/css2?family=Big+Shoulders+Display:wght@300&family=Josefin+Sans:wght@200&display=swap">
<style>
  :root {
    --cover-black: #231f20;
    --band-ice: #a3d9e3;
    --title-white: #ffffff;
  }
  html, body {
    margin: 0;
    padding: 0;
    width: 1200px;
    height: 1200px;
    overflow: hidden;
    background: var(--cover-black);
  }
  .cd-cover {
    display: block;
    width: 1200px;
    height: 1200px;
  }
  .cover-ground { fill: var(--cover-black); }
  .band-name {
    font-family: "Big Shoulders Display", "Oswald", sans-serif;
    font-weight: 300;
    fill: var(--band-ice);
    text-transform: uppercase;
  }
  .single-title {
    font-family: "Josefin Sans", "Century Gothic", sans-serif;
    font-weight: 200;
    font-size: 48px;
    fill: var(--title-white);
    text-transform: uppercase;
  }
</style>
</head>
<body>
<svg class="cd-cover" viewBox="0 0 1200 1200" xmlns="http://www.w3.org/2000/svg" role="img" aria-label="Low Ferry Guild – Wavering">
  <rect class="cover-ground" x="0" y="0" width="1200" height="1200"/>

  <g class="band-name-stack">
    <text class="band-name band-name--top" x="352" y="432" font-size="383" textLength="504" lengthAdjust="spacingAndGlyphs">Low</text>
    <text class="band-name band-name--middle" x="352" y="724" font-size="349" textLength="504" lengthAdjust="spacingAndGlyphs">Ferry</text>
    <text class="band-name band-name--bottom" x="352" y="936" font-size="234" textLength="504" lengthAdjust="spacingAndGlyphs">Guild</text>
  </g>

  <text class="single-title" x="152" y="1080" textLength="928" lengthAdjust="spacing">Wavering</text>
</svg>
</body>
</html>
```